8'x8' Exhibit Backdrop for Healthcare Events focused on the 55 and older crowds

8X8 Backdrop for Exhibiting.

I also want a design for a 6' table skirt to include our logo on two sides and the logo with Hereditary Cancer Screening underneath on the front. I want the main message of Will You Give your Loved Ones The Information To Beat Cancer in Their Lives to be completely centered on the 8X8 backdrop. Hereditary Cancer Screening The Test You Take For Them in the top left corner and the purple box on the right hand side - just like the photo that has been uploaded below. I need High resolution photos around the backdrop but not so large that they overtake the main message.

Target Market(s)

55+ crowd living in Adult only communities. They have an active lifestyle

Industry/Entity Type

Healthcare

Other font styles liked:
• "The Test You Take For Them" is Comic Sans

Colors
0255a3
fbed22
ffffff

Requirements
Must have
• I am posting a photo of the exact backdrop I would like to see. There are red arrows showing where to move certain items. There is a space underneath the slogan WILL YOU GIVE YOUR LOVED ONES... where another photo will go. Add another photo underneath the slogan that you are moving up - GIVE THEM THE GIFT OF KNOWLEDGE
• See the upload section for the new photo
• Do this one exactly like I am asking for and then you can show me some of your ideas. Thanks
• THE PHOTOS UPLOADED ARE EXAMPLES. FEEL FREE TO SEARCH OUT YOUR OWN HIGH RESOLUTION PHOTOS. THANKS

```html
<!DOCTYPE html>
<html lang="en">
<head>
<meta charset="utf-8">
<title>Hereditary Cancer Screening Backdrop</title>
<link rel="stylesheet" href="https://fonts.googleapis.com/css2?family=Bebas+Neue&family=Montserrat:wght@400;600;800&family=Oswald:wght@300;400&family=Open+Sans:wght@400&display=swap">
<style>
  :root {
    --navy: #0d1a50;
    --green: #8dc63f;
    --white: #ffffff;
    --photo-warm: #d8c2ae;
    --photo-green: #9aa85a;
    --photo-duo: #6f78a8;
  }
  html, body { margin: 0; padding: 0; overflow: hidden; background: var(--white); }
  .backdrop { position: relative; width: 1200px; height: 1200px; overflow: hidden; background: var(--white); }
  .photo { position: absolute; }

  .title { position: absolute; left: 32px; top: 38px; color: var(--navy); font-family: 'Montserrat', sans-serif; }
  .title-line { display: block; font-size: 72px; line-height: 64px; letter-spacing: -1px; }
  .title-line.strong { font-weight: 800; }
  .title-line.light { font-weight: 400; }
  .tagline { position: absolute; left: 30px; top: 266px; width: 373px; height: 44px; background: var(--green); color: var(--white);
    font-family: 'Montserrat', sans-serif; font-size: 25px; line-height: 44px; text-align: center; }

  .slogan { position: absolute; left: 376px; top: 340px; width: 428px; color: var(--navy); font-family: 'Bebas Neue', sans-serif; text-align: center; }
  .slogan-line { display: block; white-space: nowrap; }
  .slogan .ask { font-size: 76px; line-height: 96px; }
  .slogan .give { font-size: 132px; line-height: 96px; }
  .slogan .loved { font-size: 78px; line-height: 84px; margin-top: 6px; }
  .slogan .info { display: block; background: var(--navy); color: var(--white); font-family: 'Oswald', sans-serif; font-weight: 300;
    font-size: 40px; line-height: 56px; margin-top: 8px; }
  .slogan .cancer { font-size: 184px; line-height: 150px; color: var(--green); margin-top: 6px; }
  .slogan .lives { font-size: 86px; line-height: 86px; }

  .side-panel { position: absolute; left: 842px; top: 0; width: 358px; height: 830px; background: var(--navy); }
  .side-photo { left: 0; top: 0; width: 358px; height: 330px;
    background: linear-gradient(180deg, var(--photo-duo) 0%, #4c5690 65%, var(--navy) 100%); }
  .gift { position: absolute; right: 30px; top: 425px; text-align: right; color: var(--white); font-family: 'Bebas Neue', sans-serif; }
  .gift-line { display: block; white-space: nowrap; }
  .gift .bold { font-size: 70px; line-height: 62px; }
  .gift .thin { font-family: 'Oswald', sans-serif; font-weight: 300; }
  .gift .first .thin { font-size: 56px; }
  .gift .mid { font-family: 'Oswald', sans-serif; font-weight: 300; font-size: 48px; line-height: 50px; }
  .gift .note { font-family: 'Open Sans', sans-serif; font-size: 33px; line-height: 38px; margin-top: 6px; }

  .brand { position: absolute; left: 32px; top: 1060px; display: flex; align-items: center; gap: 16px; }
  .brand-dot { width: 96px; height: 96px; border-radius: 50%; background: var(--navy); }
  .brand-name { font-family: 'Montserrat', sans-serif; font-weight: 600; font-size: 32px; line-height: 36px; color: var(--navy); letter-spacing: 1px; }
</style>
</head>
<body>
<main class="backdrop">
  <header class="title">
    <span class="title-line strong">Hereditary</span>
    <span class="title-line light">Cancer</span>
    <span class="title-line light">Screening</span>
  </header>
  <div class="tagline">The Test You Take For Them</div>

  <div class="photo" style="left:438px;top:0;width:381px;height:308px;background:linear-gradient(135deg,#efe6dc,#d9c6b4 60%,#c9b08f);" role="img" aria-label="Grandmother, mother and daughter smiling together on a sofa with tea"></div>

  <aside class="side-panel">
    <div class="photo side-photo" role="img" aria-label="Grandfather smiling with grandson hugging him from behind, blue duotone"></div>
    <div class="gift">
      <span class="gift-line first"><span class="bold">Give</span> <span class="thin">Them</span></span>
      <span class="gift-line mid">The Gift Of</span>
      <span class="gift-line bold">Knowledge</span>
      <span class="gift-line note">that you will be<br>moving up.</span>
    </div>
  </aside>

  <div class="photo" style="left:0;top:345px;width:346px;height:484px;background:linear-gradient(160deg,var(--photo-green),#b8a88e 55%,#8fa3c4);" role="img" aria-label="Older woman kissing an older man's cheek outdoors"></div>

  <section class="slogan">
    <span class="slogan-line"><span class="ask">Will You</span> <span class="give">Give</span></span>
    <span class="slogan-line loved">Your Loved Ones</span>
    <span class="slogan-line info">The Information To Beat</span>
    <span class="slogan-line cancer">Cancer</span>
    <span class="slogan-line lives">In Their Lives?</span>
  </section>

  <div class="photo" style="left:0;top:847px;width:246px;height:164px;background:linear-gradient(135deg,#6d6a64,#a9a49b 60%,#d8d2c8);" role="img" aria-label="Older couple dancing together in a kitchen"></div>
  <div class="photo" style="left:262px;top:847px;width:247px;height:164px;background:linear-gradient(135deg,#5b4a2c,#c08a3a 50%,#2c2a22);" role="img" aria-label="Older men playing chess outdoors in autumn light"></div>
  <div class="photo" style="left:525px;top:850px;width:675px;height:350px;background:linear-gradient(135deg,#f1ece6,#e4cfc0 50%,#d7c3a8);" role="img" aria-label="Three-generation family smiling together on a couch"></div>

  <div class="brand">
    <div class="brand-dot"></div>
    <div class="brand-name">CLEARPATH<br>HEALTH<br>GROUP</div>
  </div>
</main>
</body>
</html>
```